Brightmill Data Works

Our company is about IT hardwares and IT solutions. IT hardware such as PC, RAMS, storage and servers. IT solutions such as project management, BA. We are also selling new technology too.

Target Market(s)

Consumer, Small to Medium Business, Corporate

Requirements
Must have
• The business card must have the following:
• Name:
• Title:
• Contact Number:
• Email address:
• Website:
• Color: Must match the logo color upgrade

```html
<!DOCTYPE html>
<html lang="en">
<head>
<meta charset="UTF-8">
<title>Brightmill Data Works — Business Card</title>
<link href="https://fonts.googleapis.com/css2?family=Oswald:wght@500&family=Work+Sans:wght@400;700&display=swap" rel="stylesheet">
<style>
  :root {
    --backdrop: #1c1c1c;
    --card: #1f1f1f;
    --card-light: #2c2c2c;
    --amber: #e89a36;
    --white: #f4f4f4;
  }
  * { margin: 0; padding: 0; box-sizing: border-box; }
  html, body { width: 1200px; height: 900px; overflow: hidden; }
  body {
    background: var(--backdrop);
    font-family: "Work Sans", sans-serif;
    color: var(--white);
    display: flex;
    flex-direction: column;
    align-items: center;
    justify-content: center;
    gap: 40px;
  }
  .card {
    position: relative;
    width: 660px;
    height: 377px;
    background: linear-gradient(135deg, var(--card) 0%, var(--card) 55%, var(--card-light) 100%);
    border-bottom: 4px solid var(--amber);
    box-shadow: 0 14px 30px rgba(0,0,0,0.55);
  }
  .card-front {
    display: flex;
    align-items: center;
    justify-content: center;
  }
  .brand {
    display: flex;
    align-items: center;
    gap: 16px;
  }
  .brand-mark {
    width: 26px;
    height: 26px;
    background: var(--amber);
  }
  .brand-name {
    font-weight: 700;
    font-size: 38px;
    letter-spacing: 1px;
    text-transform: uppercase;
    color: var(--white);
  }
  .card-back .identity {
    position: absolute;
    right: 380px;
    top: 150px;
    text-align: right;
  }
  .person-name {
    font-family: "Oswald", sans-serif;
    font-weight: 500;
    font-size: 38px;
    line-height: 1;
    color: var(--amber);
    text-transform: uppercase;
    white-space: nowrap;
  }
  .person-title {
    margin-top: 6px;
    font-size: 18px;
    color: var(--white);
  }
  .divider {
    position: absolute;
    left: 300px;
    top: 150px;
    width: 2px;
    height: 66px;
    background: var(--white);
  }
  .contact-list {
    position: absolute;
    left: 324px;
    top: 146px;
    list-style: none;
    font-size: 17px;
    line-height: 25px;
  }
  .contact-list li {
    display: flex;
    align-items: center;
    gap: 10px;
    white-space: nowrap;
  }
  .contact-list svg { width: 13px; height: 13px; flex: none; }
  .accent { color: var(--amber); }
  .address {
    position: absolute;
    left: 50px;
    bottom: 32px;
    font-size: 18px;
    letter-spacing: 0.3px;
  }
</style>
</head>
<body>
  <section class="card card-front">
    <div class="brand">
      <span class="brand-mark"></span>
      <span class="brand-name">Brightmill Data Works</span>
    </div>
  </section>

  <section class="card card-back">
    <div class="identity">
      <p class="person-name">Daniel Whitaker</p>
      <p class="person-title">Director</p>
    </div>
    <span class="divider"></span>
    <ul class="contact-list">
      <li>
        <svg viewBox="0 0 24 24" fill="none" stroke="#e89a36" stroke-width="2.2"><path d="M5 3h4l2 5-3 2a12 12 0 0 0 6 6l2-3 5 2v4a2 2 0 0 1-2 2A18 18 0 0 1 3 5a2 2 0 0 1 2-2z"/></svg>
        <span>555-014-2873</span>
      </li>
      <li>
        <svg viewBox="0 0 24 24" fill="none" stroke="#e89a36" stroke-width="2.2"><rect x="2" y="5" width="20" height="14"/><path d="M2 6l10 7 10-7"/></svg>
        <span>hello@brightmilldata.com</span>
      </li>
      <li>
        <svg viewBox="0 0 24 24" fill="none" stroke="#e89a36" stroke-width="2"><circle cx="12" cy="12" r="10"/><path d="M2 12h20M12 2c3 3 3 17 0 20M12 2c-3 3-3 17 0 20"/></svg>
        <span>www.<span class="accent">brightmilldata</span>.com</span>
      </li>
    </ul>
    <p class="address">820 Alder Creek Way Fairhaven, CA 95012-4410</p>
  </section>
</body>
</html>
```